Local Flower Farm Needs Business Card Design

I need business cards designed for a flower farm based in Eudora, Kansas.
Business Info:
We are a local cut flower farm located in Eudora, Kansas, founded by Corinne Haldwick. What started as a passion for agriculture and search for more joy in daily life has blossomed into a small business dedicated to providing the community with beautiful, fresh, and sustainable flowers. We specialize in local, seasonal blooms, ensuring that every petal reflects the care and dedication we pour into our craft. Our mission is to deliver the highest quality flowers directly to our customers through local farmers markets and to florists who share our commitment to sustainability. Join us in celebrating the beauty of nature, one bloom at a time!
Contact Details:
Corinne Haldwick
Owner
Phone 913-555-0147
Facebook: Rosalind Thorpe Gardens
Instagram: @RosalindThorpeGardens
Website: RosalindThorpeGardens.example
Target Market(s)
Wholesale to Florists and Direct to Consumer via Farmers Market
Industry/Entity Type
Florist, Farm
Contact Information for Business Card
Name, Contact Info, Logo
Look and feel
Each slider illustrates characteristics of the customer's brand and the style your logo design should communicate.

```html
<!DOCTYPE html>
<html lang="en">
<head>
<meta charset="utf-8">
<title>Rosalind Thorpe Gardens – Business Card</title>
<link rel="stylesheet" href="https://fonts.googleapis.com/css2?family=Cormorant+Garamond:wght@500&family=Montserrat:wght@300;400;700&display=swap">
<style>
  :root {
    --backdrop: #1b1c1d;
    --card: #0e2a2f;
    --card-edge: #12343a;
    --ink: #ffffff;
    --ink-soft: #dfe8e9;
    --teal-glow: #3f7f86;
    --teal-deep: #0b2227;
  }
  * { box-sizing: border-box; margin: 0; padding: 0; }
  html, body {
    width: 1200px; height: 988px; overflow: hidden;
    background: var(--backdrop);
  }
  .card {
    position: absolute;
    width: 560px; height: 320px;
    border-radius: 22px;
    background: var(--card);
    box-shadow: 0 0 0 1px var(--card-edge), 0 24px 40px rgba(0,0,0,.55);
    overflow: hidden;
  }
  .card--front { left: 60px; top: 140px; }
  .card--back  { left: 580px; top: 520px; }

  /* Front */
  .seal {
    position: absolute; left: 50%; top: 50%;
    width: 236px; height: 236px;
    transform: translate(-50%, -50%);
  }
  .seal svg { position: absolute; inset: 0; }
  .seal__name {
    position: absolute; inset: 0;
    display: flex; align-items: center; justify-content: center;
    text-align: center;
    font-family: "Cormorant Garamond", serif;
    font-weight: 500;
    font-size: 22px; line-height: 1.25;
    letter-spacing: 3px; text-transform: uppercase;
    color: var(--ink);
  }

  /* Back */
  .monogram-area {
    position: absolute; left: 360px; top: 26px;
    width: 170px; height: 190px; border-radius: 14px;
    background: linear-gradient(160deg, var(--teal-glow), var(--teal-deep) 80%);
    opacity: .5;
  }
  .holder {
    position: absolute; left: 48px; top: 62px;
    font-family: "Montserrat", sans-serif; color: var(--ink);
  }
  .holder__name {
    font-weight: 700; font-size: 22px; line-height: 28px;
    letter-spacing: 1px; text-transform: uppercase; white-space: nowrap;
  }
  .holder__rule--long {
    position: absolute; left: 150px; top: 34px;
    width: 180px; height: 1.5px; background: var(--ink);
  }
  .holder__role {
    font-weight: 300; font-size: 13px; line-height: 18px;
    letter-spacing: 1px; margin-top: 2px; color: var(--ink-soft);
  }
  .holder__rule--short {
    display: block; width: 110px; height: 2px;
    background: var(--ink); margin-top: 6px;
  }

  .contacts {
    position: absolute; left: 62px; top: 150px;
    font-family: "Montserrat", sans-serif; font-weight: 400;
    font-size: 13px; color: var(--ink);
  }
  .contacts__list { list-style: none; }
  .contacts__list li {
    display: flex; align-items: center; gap: 9px;
    height: 21px; white-space: nowrap;
  }
  .contacts__list svg { width: 12px; height: 12px; flex: none; }
  .contacts__divider {
    width: 10px; height: 1.5px; background: var(--ink);
    margin: 10px 0 10px 1px;
  }
  .social-dot {
    width: 11px; height: 11px; border-radius: 50%;
    background: var(--ink); flex: none;
  }
</style>
</head>
<body>

<section class="card card--front" aria-label="Card front">
  <div class="seal">
    <svg viewBox="0 0 236 236" aria-hidden="true">
      <circle cx="118" cy="118" r="116" fill="none" stroke="#ffffff" stroke-width="1.2"/>
    </svg>
    <p class="seal__name">Rosalind<br>Thorpe<br>Gardens</p>
  </div>
</section>

<section class="card card--back" aria-label="Card back">
  <div class="monogram-area" role="img" aria-label="Large faint brand monogram with floral sprigs"></div>

  <div class="holder">
    <h1 class="holder__name">Corinne Haldwick</h1>
    <span class="holder__rule--long" aria-hidden="true"></span>
    <p class="holder__role">OWNER</p>
    <span class="holder__rule--short" aria-hidden="true"></span>
  </div>

  <div class="contacts">
    <ul class="contacts__list">
      <li>
        <svg viewBox="0 0 24 24" aria-hidden="true"><path fill="#fff" d="M6.6 10.8a15.1 15.1 0 0 0 6.6 6.6l2.2-2.2a1 1 0 0 1 1-.25 11.4 11.4 0 0 0 3.6.57 1 1 0 0 1 1 1V20a1 1 0 0 1-1 1A17 17 0 0 1 3 4a1 1 0 0 1 1-1h3.5a1 1 0 0 1 1 1c0 1.25.2 2.45.57 3.6a1 1 0 0 1-.25 1z"/></svg>
        913-555-0147
      </li>
      <li>
        <svg viewBox="0 0 24 24" aria-hidden="true"><rect x="2" y="5" width="20" height="14" rx="2" fill="#fff"/><path d="M3 6l9 7 9-7" fill="none" stroke="#0e2a2f" stroke-width="2"/></svg>
        info@RosalindThorpeGardens.example
      </li>
      <li>
        <svg viewBox="0 0 24 24" aria-hidden="true"><circle cx="12" cy="12" r="10" fill="none" stroke="#fff" stroke-width="2"/><path d="M2 12h20M12 2c3 3 3 17 0 20M12 2c-3 3-3 17 0 20" fill="none" stroke="#fff" stroke-width="1.6"/></svg>
        www.RosalindThorpeGardens.example
      </li>
    </ul>
    <div class="contacts__divider" aria-hidden="true"></div>
    <ul class="contacts__list">
      <li><span class="social-dot" aria-hidden="true"></span>Rosalind Thorpe Gardens</li>
      <li><span class="social-dot" aria-hidden="true"></span>@RosalindThorpeGardens</li>
    </ul>
  </div>
</section>

</body>
</html>
```